Business Card Design for company

We want new business cards. We'd like something different-- yet still highly professional. Our tagline is Guiding strategy, building results. Stock photos are ok, as long as they are relevant and look upscale.

Target Market(s)

Architecture/Business Management Consulting/Engineering Consulting

Contact Information for Business Card

dark gray background with pops of blue might be good, but you tell me. You're the designers. Rounded corners might be nice, but again, you tell me.

Font styles to use
Serif
Sans Serif

Colors
3276b5
5c5c5c
9d9d9d
fbfbfb

Requirements
Nice to have
• Something different, but still very professional.

```html
<!DOCTYPE html>
<html lang="en">
<head>
<meta charset="utf-8">
<title>Veyra Partners — Business Cards</title>
<link rel="stylesheet" href="https://fonts.googleapis.com/css2?family=Roboto:wght@400;500;700&display=swap">
<style>
  :root {
    --brand-blue: #26619a;
    --charcoal: #4a4d52;
    --rule-gray: #5c5c5c;
    --paper: #ffffff;
    --canvas: #e9e9ea;
    --ink-light: #ffffff;
  }
  * { margin: 0; padding: 0; box-sizing: border-box; }
  html, body {
    width: 1200px; height: 1108px; overflow: hidden;
    background: var(--canvas);
    font-family: "Roboto", Arial, sans-serif;
  }
  .sheet { position: relative; width: 1200px; height: 1108px; }
  .card {
    position: absolute; left: 250px; width: 700px; height: 400px;
    overflow: hidden;
    box-shadow: 0 6px 18px rgba(0,0,0,0.18);
  }
  /* Back of card */
  .card-back { top: 100px; background: var(--charcoal); }
  .card-back .wordmark {
    position: absolute; top: 146px; left: 0; width: 100%;
    text-align: center; color: var(--brand-blue);
    font-weight: 700; font-size: 64px; letter-spacing: 3px; line-height: 1;
  }
  .card-back .tagline {
    position: absolute; top: 262px; left: 0; width: 100%;
    text-align: center; color: var(--ink-light);
    font-size: 17px; letter-spacing: 0.5px;
  }
  .tagline .dot {
    display: inline-block; width: 7px; height: 7px; border-radius: 50%;
    background: var(--ink-light); margin: 0 10px; vertical-align: middle;
  }
  /* Front of card */
  .card-front { top: 608px; background: var(--paper); }
  .card-front .band { position: absolute; inset: 0; }
  .card-front .wordmark {
    position: absolute; top: 74px; left: 0; width: 100%;
    text-align: center; color: var(--brand-blue);
    font-weight: 700; font-size: 54px; letter-spacing: 3px; line-height: 1;
  }
  .identity {
    position: absolute; left: 34px; top: 252px; color: var(--ink-light);
  }
  .identity .name { font-weight: 700; font-size: 23px; letter-spacing: 0.5px; }
  .identity .role { font-size: 17px; margin-bottom: 12px; }
  .identity .address { font-size: 16px; line-height: 21px; }
  .contacts {
    position: absolute; right: 22px; top: 262px;
    list-style: none; color: var(--ink-light); font-size: 17px;
  }
  .contacts li {
    display: flex; justify-content: flex-end; align-items: center;
    height: 24px; gap: 12px;
  }
  .contacts svg { width: 18px; height: 18px; fill: var(--ink-light); flex: none; }
</style>
</head>
<body>
<main class="sheet">
  <section class="card card-back" aria-label="Card back">
    <div class="wordmark">VEYRA PARTNERS</div>
    <p class="tagline">Guiding strategy<span class="dot"></span>building results</p>
  </section>

  <section class="card card-front" aria-label="Card front">
    <svg class="band" viewBox="0 0 700 400" width="700" height="400" aria-hidden="true">
      <path d="M0 212 H150 L166 232 H214 L230 212 H700" fill="none" stroke="var(--rule-gray)" stroke-width="5"/>
      <path d="M0 220 H146 L162 240 H218 L234 220 H700 V400 H0 Z" fill="var(--brand-blue)"/>
    </svg>

    <div class="wordmark">VEYRA PARTNERS</div>

    <div class="identity">
      <p class="name">DANIEL MOREAU</p>
      <p class="role">CEO/FOUNDER</p>
      <p class="address">1420 Harbor View Road<br>Juneau, Alaska 99801</p>
    </div>

    <ul class="contacts">
      <li>555 210 4837
        <svg viewBox="0 0 24 24"><path d="M6.6 10.8a15 15 0 0 0 6.6 6.6l2.2-2.2c.3-.3.7-.4 1-.2 1.1.4 2.3.6 3.6.6.6 0 1 .4 1 1V20c0 .6-.4 1-1 1A17 17 0 0 1 3 4c0-.6.4-1 1-1h3.5c.6 0 1 .4 1 1 0 1.3.2 2.5.6 3.6.1.3 0 .7-.2 1z"/></svg>
      </li>
      <li>555 362 7190
        <svg viewBox="0 0 24 24"><path d="M7 1h10a2 2 0 0 1 2 2v18a2 2 0 0 1-2 2H7a2 2 0 0 1-2-2V3a2 2 0 0 1 2-2zm0 3v14h10V4zm5 15.5a1 1 0 1 0 0 2 1 1 0 0 0 0-2z"/></svg>
      </li>
      <li>555 481 0526
        <svg viewBox="0 0 24 24"><path d="M6 2h12v6H6zM3 9h18a1 1 0 0 1 1 1v8h-4v4H6v-4H2v-8a1 1 0 0 1 1-1zm5 7v4h8v-4z"/></svg>
      </li>
      <li>daniel@veyrapartners.com
        <svg viewBox="0 0 24 24"><path d="M2 5h20v14H2zm2 2v.5l8 5 8-5V7zm0 2.8V17h16V9.8l-8 5z"/></svg>
      </li>
      <li>www.veyrapartners.com
        <svg viewBox="0 0 24 24"><path d="M12 2a10 10 0 1 0 0 20 10 10 0 0 0 0-20zm0 2c.9 0 2.2 1.8 2.8 5H9.2C9.8 5.8 11.1 4 12 4zm-3 7h6a17 17 0 0 1 0 2H9a17 17 0 0 1 0-2zm-4.9 0h2.9a19 19 0 0 0 0 2H4.1a8 8 0 0 1 0-2zm12.9 0h2.9a8 8 0 0 1 0 2H17a19 19 0 0 0 0-2zM9.2 15h5.6c-.6 3.2-1.9 5-2.8 5s-2.2-1.8-2.8-5z"/></svg>
      </li>
    </ul>
  </section>
</main>
</body>
</html>
```